Psychiatric Office Needs a Website- 1st Time Ever!

Been in practice since 2003 with no website, but finally ready to dive in. We are Maplecrest Behavioral Healthcare, a mental health outpatient practice based in Fayetteville, Georgia that sees diverse individuals and families from childhood to advanced age for a variety of conditions. We've grown by word of mouth and referral but would now like to have a digital footprint. Be the pioneer of our website and we will be sure to share. We would like to see designs that are modern, animated, fairly colorful, easy to read, and caters to all ages. Also, we would like the design to take the whole page (not be centered) and can be viewed well on phone/tablet. Please see our outline for more information. Our motto/slogan is: Maplecrest Behavioral Healthcare- A step forward in your wellness journey, so the design should try to reflect that.
Updates

Project Deadline Extended
Reason: site in progress

Target Market(s)

Children through elderly

Industry/Entity Type

Medical

Logo Text

Stepping forward in your wellness journey

Number of Pages Required

1 page

Colors

Designer to choose colors to be used in the design.

Requirements
Must have
• Animation or moving pictures.
• Color.
• Concise.
• User friendly
• Diversity in the stock photos

```html
<!DOCTYPE html>
<html lang="en">
<head>
<meta charset="utf-8">
<title>Maplecrest Behavioral Healthcare</title>
<link rel="stylesheet" href="https://fonts.googleapis.com/css2?family=Asap:ital,wght@0,400;0,500;1,400&family=Arimo:wght@400;700&display=swap">
<style>
:root{
  --magenta:#a3237e;
  --magenta-dark:#7c195f;
  --magenta-light:#c04a9c;
  --ink:#333333;
  --muted:#666666;
  --white:#ffffff;
  --dark:#262626;
  --line:#d9d9d9;
}
*{box-sizing:border-box;margin:0;padding:0}
html,body{width:1200px;height:3455px;overflow:hidden}
body{font-family:"Arimo",Arial,sans-serif;color:var(--ink);background:var(--white)}
.page{position:relative;width:1200px;height:3455px;overflow:hidden}
.abs{position:absolute}
h1,h2,h3,.nav a,.btn{font-family:"Asap",Helvetica,sans-serif;font-weight:400}
p{font-size:14px;line-height:21px}

/* header */
.header{position:absolute;left:0;top:0;width:1200px;height:127px;background:var(--white)}
.topinfo{position:absolute;top:12px;font-size:13px;color:var(--ink);display:flex;align-items:center;gap:7px}
.topinfo svg{width:16px;height:16px}
.brand{position:absolute;left:83px;top:10px;display:flex;align-items:center;gap:12px}
.brand-dot{width:100px;height:100px;border-radius:50%;background:var(--magenta);border:4px solid #e7c4dc}
.brand-name{font-family:"Asap",sans-serif;font-size:16px;line-height:20px;color:var(--magenta);width:150px}
.nav a{position:absolute;top:76px;font-size:16px;color:var(--ink);text-decoration:none}
.nav .active{left:357px;top:41px;width:104px;height:79px;background:var(--magenta);color:var(--white);text-align:center;padding-top:35px}

/* hero */
.hero{position:absolute;left:0;top:127px;width:1200px;height:563px;background:linear-gradient(180deg,#9fae8c 0%,#6f7f5a 45%,#3d3a30 80%,#2c2b26 100%)}
.hero-title{position:absolute;left:0;width:1200px;top:174px;text-align:center;color:var(--white)}
.hero-title h1{font-size:50px;line-height:60px;display:inline-block;background:rgba(60,60,60,.35);padding:0 8px}
.hero-title p{font-family:"Asap",sans-serif;font-style:italic;font-size:23px;margin-top:2px}
.btn{display:inline-block;background:var(--magenta);color:var(--white);text-decoration:none;font-size:19px;text-align:center}
.hero .btn{position:absolute;left:507px;top:281px;width:184px;height:53px;line-height:53px}

/* vision / mission */
.vm{position:absolute;left:0;top:690px;width:1200px;height:370px}
.vm-left{position:absolute;left:0;top:0;width:600px;height:370px;background:var(--magenta)}
.vm h2{position:absolute;top:50px;font-size:36px;display:flex;align-items:center;gap:14px}
.vm h2 svg{width:36px;height:36px}
.vm-left h2{left:78px;color:var(--white);border-bottom:2px solid rgba(255,255,255,.6);padding-bottom:4px}
.vm-right h2{left:771px;color:var(--magenta)}
.vm p{position:absolute;top:124px;font-size:14.5px;line-height:24px}
.vm-left p{left:78px;width:355px;color:var(--white)}
.vm-right p{left:771px;width:350px;color:var(--muted)}
.vm-seal{position:absolute;left:465px;top:21px;width:268px;height:268px;border-radius:50%;background:var(--magenta);border:8px solid var(--white);box-shadow:0 0 0 3px var(--magenta);display:flex;align-items:center;justify-content:center;text-align:center;color:var(--white);font-family:"Asap",sans-serif;font-size:24px;line-height:30px;padding:30px}

/* services */
.services{position:absolute;left:0;top:1060px;width:1200px;height:833px;background:linear-gradient(135deg,#4a4a4a 0%,#2e2e2e 50%,#3b3b3b 100%)}
.section-title{position:absolute;left:0;width:1200px;text-align:center;font-size:34px;color:var(--white)}
.section-title span{border-bottom:2px solid rgba(255,255,255,.7);padding:0 6px 6px}
.svc{position:absolute;color:var(--white);width:300px}
.svc h3{font-family:"Arimo",sans-serif;font-size:16px;margin-bottom:4px}
.svc p{font-size:13px;line-height:18px}
.svc a{color:var(--white);font-weight:700}

/* conditions */
.conditions{position:absolute;left:0;top:1893px;width:1200px;height:548px;background:linear-gradient(135deg,var(--magenta-light) 0%,var(--magenta) 50%,var(--magenta-dark) 100%)}
.card{position:absolute;top:150px;width:253px;color:var(--white);text-align:center}
.card .photo{width:253px;height:168px;box-shadow:0 6px 12px rgba(0,0,0,.3)}
.card h3{font-size:20px;line-height:22px;margin-top:24px;height:44px}
.card p{font-size:13px;line-height:18px;margin-top:0}
.arrow{position:absolute;top:2106px;width:30px;height:30px;background:var(--white)}
.dots{position:absolute;top:2410px;left:574px;display:flex;gap:4px}
.dots i{width:14px;height:14px;border:2px solid var(--white);display:block}
.dots .on{background:var(--white)}

/* faq & news */
.col-title{position:absolute;top:2493px;font-size:36px;color:var(--magenta)}
.divider{position:absolute;left:610px;top:2446px;width:4px;height:428px;background:#ececec}
.faq-item{position:absolute;left:78px;width:520px;border:1px solid var(--line);display:flex;align-items:center;gap:14px;padding-left:14px;font-family:"Asap",sans-serif;font-size:19px;color:var(--magenta);height:40px}
.faq-open{height:127px;flex-direction:column;align-items:flex-start;gap:0;padding:0}
.faq-open .q{height:40px;display:flex;align-items:center;gap:14px;padding-left:14px;border-bottom:1px solid var(--line);width:100%}
.faq-open p{font-family:"Arimo",sans-serif;font-size:12px;line-height:18px;color:var(--ink);padding:8px 16px}
.news{position:absolute;left:668px;width:460px}
.news .thumb{position:absolute;left:0;top:0;width:115px;height:111px}
.news h3{position:absolute;left:130px;top:0;font-size:19px;color:var(--magenta);white-space:nowrap}
.news .date{position:absolute;left:130px;top:30px;font-size:11px;color:var(--muted)}
.news p{position:absolute;left:130px;top:48px;width:330px;font-size:13px;line-height:19px;color:var(--muted)}
.news .more{position:absolute;left:130px;top:95px;font-size:13px;color:var(--magenta);letter-spacing:.5px}
.news-rule{position:absolute;left:668px;top:2686px;width:460px;height:1px;background:var(--line)}

/* band */
.band{position:absolute;left:0;top:2874px;width:1200px;height:108px;background:linear-gradient(90deg,var(--magenta-light),var(--magenta) 40%,var(--magenta-dark))}
.band p{position:absolute;left:78px;top:30px;width:790px;color:var(--white);font-size:14px;line-height:22px}
.band .btn{position:absolute;left:896px;top:26px;width:226px;height:55px;line-height:55px;background:var(--white);color:var(--magenta);font-size:20px}

/* footer */
.footer{position:absolute;left:0;top:2982px;width:1200px;height:399px;background:linear-gradient(135deg,#8a3a6c 0%,#5c2448 50%,#6b2c55 100%)}
.footer h3{position:absolute;top:38px;font-size:21px;color:var(--white);letter-spacing:.5px}
.field{position:absolute;left:78px;width:449px;height:41px;background:var(--white);font-size:13px;color:#666;padding:10px 12px}
.footer .submit{position:absolute;left:78px;top:343px;width:187px;height:51px;line-height:51px;font-size:19px;background:var(--magenta);color:var(--white)}
.links{position:absolute;left:569px;top:88px;list-style:none}
.links li{font-size:14px;color:var(--white);line-height:28.5px;display:flex;align-items:center;gap:12px}
.links li::before{content:"";width:8px;height:8px;border-radius:50%;background:var(--magenta-light)}
.find{position:absolute;left:873px;color:var(--white);font-size:14px;line-height:21px;display:flex;gap:16px}
.find svg{width:24px;height:24px;flex:none}
.social{position:absolute;top:3324px;width:54px;height:54px;border-radius:50%;background:var(--magenta)}
.copyright{position:absolute;left:0;top:3381px;width:1200px;height:74px;background:#3a1a2f;border-top:2px solid rgba(255,255,255,.6);color:var(--white);text-align:center;font-size:13px;line-height:70px;letter-spacing:.3px}
</style>
</head>
<body>
<div class="page">

  <header class="header">
    <div class="brand">
      <div class="brand-dot"></div>
      <div class="brand-name">Maplecrest Behavioral Healthcare</div>
    </div>
    <div class="topinfo" style="left:505px">
      <svg viewBox="0 0 16 16"><circle cx="8" cy="8" r="7" fill="var(--magenta)"/><path d="M8 4v4l3 2" stroke="#fff" stroke-width="1.6" fill="none"/></svg>
      Monday - Friday : 10.00 A.M to 8.00 P.M
    </div>
    <div class="topinfo" style="left:822px">
      <svg viewBox="0 0 16 16"><circle cx="8" cy="8" r="7" fill="var(--magenta)"/><path d="M5 4.5c0 4 2.5 6.5 6.5 7l1-1.8-2-1-1 .8c-1-.5-2-1.5-2.5-2.5l.8-1-1-2z" fill="#fff"/></svg>
      +1-555-014-2280
    </div>
    <div class="topinfo" style="left:980px">LOGIN</div>
    <div class="topinfo" style="left:1040px">
      <svg viewBox="0 0 16 16"><circle cx="8" cy="5" r="3.2" fill="var(--magenta)"/><path d="M2 15c0-4 2.7-6 6-6s6 2 6 6z" fill="var(--magenta)"/></svg>
      Patient
    </div>
    <nav class="nav">
      <a class="active" href="#">Home</a>
      <a href="#" style="left:504px">About Us</a>
      <a href="#" style="left:606px">Services</a>
      <a href="#" style="left:700px">Conditions We Treat</a>
      <a href="#" style="left:889px">New Patients</a>
      <a href="#" style="left:1020px">Contact Us</a>
    </nav>
  </header>

  <section class="hero" role="img" aria-label="Photo of two people sitting on a park bench with arms around each other, trees in soft sunlight behind">
    <div class="hero-title">
      <h1>Maplecrest Behavioral Healthcare</h1>
      <p>A step forward in your wellness journey</p>
    </div>
    <a class="btn" href="#">CONTACT US</a>
  </section>

  <section class="vm">
    <div class="vm-left">
      <h2><svg viewBox="0 0 36 36"><path d="M6 20l20-10 3 6-20 10z" fill="#fff"/><path d="M16 24l-5 10M18 24l5 10" stroke="#fff" stroke-width="2.5"/></svg>VISION</h2>
      <p>Lorem Ipsum is simply dummy text of the printing and typesetting industry. Lorem Ipsum has been the industry's standard dummy text ever since the 1500s, when an unknown printer took a galley of type and scrambled it to make a type specimen book. It has survived not only five centuries, but also the leap into electronic typesetting, remaining essentially unchanged.</p>
    </div>
    <div class="vm-right">
      <h2><svg viewBox="0 0 36 36" fill="none" stroke="var(--magenta)" stroke-width="3"><circle cx="17" cy="19" r="14"/><circle cx="17" cy="19" r="7"/><path d="M17 19L32 4"/></svg>MISSION</h2>
      <p>Lorem Ipsum is simply dummy text of the printing and typesetting industry. Lorem Ipsum has been the industry's standard dummy text ever since the 1500s, when an unknown printer took a galley of type and scrambled it to make a type specimen book. It has survived not only five centuries, but also the leap into electronic typesetting, remaining essentially unchanged.</p>
    </div>
    <div class="vm-seal">Maplecrest Behavioral Healthcare</div>
  </section>

  <section class="services" role="img" aria-label="Dimmed background photo of a counselling session">
    <h2 class="section-title" style="top:46px"><span>SERVICES</span></h2>
    <svg class="abs" style="left:0;top:0" width="1200" height="833" viewBox="0 1060 1200 833">
      <g stroke="#d9a9c9" stroke-width="2">
        <line x1="599" y1="1446" x2="488" y2="1255"/><line x1="599" y1="1446" x2="689" y2="1250"/>
        <line x1="599" y1="1446" x2="394" y2="1414"/><line x1="599" y1="1446" x2="799" y2="1396"/>
        <line x1="599" y1="1446" x2="442" y2="1589"/><line x1="599" y1="1446" x2="767" y2="1582"/>
        <line x1="599" y1="1446" x2="606" y2="1663"/>
      </g>
      <circle cx="599" cy="1446" r="104" fill="#eeeeee" stroke="#cfcfcf" stroke-width="6"/>
      <g fill="#e8c7dd" stroke="var(--magenta)" stroke-width="6">
        <circle cx="488" cy="1255" r="60"/><circle cx="689" cy="1250" r="60"/>
        <circle cx="394" cy="1414" r="60"/><circle cx="799" cy="1396" r="60"/>
        <circle cx="442" cy="1589" r="60"/><circle cx="767" cy="1582" r="60"/>
        <circle cx="606" cy="1663" r="60"/>
      </g>
    </svg>
    <div class="svc" style="left:138px;top:157px"><h3>Diagnostic evaluation and treatment</h3><p>Lorem Ipsum is simply dummy text<br>of the printing and text typesetting<br>industry.<a href="#">READ MORE</a></p></div>
    <div class="svc" style="left:771px;top:140px"><h3>Disability and work-related reports</h3><p>Lorem Ipsum is simply dummy text<br>of the printing and text typesetting<br>industry.<a href="#">READ MORE</a></p></div>
    <div class="svc" style="left:81px;top:324px"><h3>Psychopharmacology</h3><p>Lorem Ipsum is simply dummy text<br>of the printing and text typesetting<br>industry.<a href="#">READ MORE</a></p></div>
    <div class="svc" style="left:887px;top:297px"><h3>Early childhood Assessments</h3><p>Lorem Ipsum is simply dummy text of<br>the printing and text typesetting<br>industry.<a href="#">READ MORE</a></p></div>
    <div class="svc" style="left:101px;top:513px"><h3>Bariatric pre-surgical consultation</h3><p>Lorem Ipsum is simply dummy text of<br>the printing and text typesetting<br>industry.<a href="#">READ MORE</a></p></div>
    <div class="svc" style="left:864px;top:486px"><h3>Substance abuse assessments</h3><p>Lorem Ipsum is simply dummy text of<br>the printing and text typesetting<br>industry.<a href="#">READ MORE</a></p></div>
    <div class="svc" style="left:502px;top:690px"><h3>Developmental disabilities</h3><p>Lorem Ipsum is simply dummy<br>text of the printing and text<br>typesetting industry.<a href="#">READ MORE</a></p></div>
  </section>

  <section class="conditions">
    <h2 class="section-title" style="top:60px"><span>CONDITIOND WE TREAT</span></h2>
    <div class="card" style="left:78px"><div class="photo" role="img" aria-label="Photo of a woman holding her head in distress" style="background:linear-gradient(135deg,#5a4a44,#2a2522)"></div><h3>Mood Disorders</h3><p>Lorem Ipsum is simply dummy text of the printing and typesetting industry. Lorem Ipsum has been the industry's standard dummy text ever since.</p></div>
    <div class="card" style="left:343px"><div class="photo" role="img" aria-label="Photo of a counsellor comforting a client" style="background:linear-gradient(135deg,#c9b6a4,#4d7ea6)"></div><h3>Anxiety Disorders</h3><p>Lorem Ipsum is simply dummy text of the printing and typesetting industry. Lorem Ipsum has been the industry's standard dummy text ever since.</p></div>
    <div class="card" style="left:608px"><div class="photo" role="img" aria-label="Photo of a therapist talking with an older man" style="background:linear-gradient(135deg,#b9a690,#6b5b4e)"></div><h3>Psychotic Disorders</h3><p>Lorem Ipsum is simply dummy text of the printing and typesetting industry. Lorem Ipsum has been the industry's standard dummy text ever since.</p></div>
    <div class="card" style="left:873px"><div class="photo" role="img" aria-label="Photo of a mother hugging her young child" style="background:linear-gradient(135deg,#a47a5c,#e3c7a8)"></div><h3>Common Disorders<br>of Childhood</h3><p>Lorem Ipsum is simply dummy text of the printing and typesetting industry. Lorem Ipsum has been the industry's standard dummy text ever since.</p></div>
  </section>
  <div class="arrow" style="left:31px"><svg viewBox="0 0 30 30" width="30" height="30"><path d="M18 9l-6 6 6 6" stroke="var(--magenta)" stroke-width="2.5" fill="none"/></svg></div>
  <div class="arrow" style="left:1138px"><svg viewBox="0 0 30 30" width="30" height="30"><path d="M12 9l6 6-6 6" stroke="var(--magenta)" stroke-width="2.5" fill="none"/></svg></div>
  <div class="dots"><i></i><i class="on"></i><i></i></div>

  <section>
    <h2 class="col-title" style="left:78px">FAQ</h2>
    <div class="faq-item faq-open" style="top:2556px">
      <div class="q"><svg width="16" height="16" viewBox="0 0 16 16"><rect x="1" y="6.5" width="14" height="3" fill="var(--magenta)"/></svg>What do I need to bring with me to my first visit?</div>
      <p>Lorem Ipsum is simply dummy text of the printing and typesetting industry. Lorem Ipsum has been the industry's standard dummy text ever since the 1500s.It has survived not only five centuries, but also the leap into electronic typesetting, remaining essentially unchanged.</p>
    </div>
    <div class="faq-item" style="top:2684px"><svg width="16" height="16" viewBox="0 0 16 16"><path d="M6.5 1h3v14h-3zM1 6.5h14v3H1z" fill="var(--magenta)"/></svg>How long do I have to wait to be seen?</div>
    <div class="faq-item" style="top:2728px"><svg width="16" height="16" viewBox="0 0 16 16"><path d="M6.5 1h3v14h-3zM1 6.5h14v3H1z" fill="var(--magenta)"/></svg>Why is my child not doing well in school?</div>
    <div class="faq-item" style="top:2772px"><svg width="16" height="16" viewBox="0 0 16 16"><path d="M6.5 1h3v14h-3zM1 6.5h14v3H1z" fill="var(--magenta)"/></svg>What typs of insurance do you accept?</div>

    <div class="divider"></div>

    <h2 class="col-title" style="left:668px">LATEST NEWS</h2>
    <article class="news" style="top:2552px">
      <div class="thumb" role="img" aria-label="Photo of a stressed young woman" style="background:linear-gradient(135deg,#9aa8b8,#51607a)"></div>
      <h3>Lorem Ipsum is simply dummy text</h3>
      <div class="date">&#9635; 10 JULY 2016</div>
      <p>Lorem Ipsum is simply dummy text of the printing and typesetting industry......</p>
      <div class="more">READ MORE &nbsp;&nbsp;&nbsp;&#187;</div>
    </article>
    <div class="news-rule"></div>
    <article class="news" style="top:2713px">
      <div class="thumb" role="img" aria-label="Photo of a family reading together" style="background:linear-gradient(135deg,#d8c2a0,#8a6a4c)"></div>
      <h3>Lorem Ipsum is simply dummy text</h3>
      <div class="date">&#9635; 10 JULY 2016</div>
      <p>Lorem Ipsum is simply dummy text of the printing and typesetting industry......</p>
      <div class="more">READ MORE &nbsp;&nbsp;&nbsp;&#187;</div>
    </article>
  </section>

  <section class="band">
    <p>Lorem Ipsum is simply dummy text of the printing and typesetting industry. Lorem Ipsum has been the industry's standard dummy text ever since the 1500s, when an unknown printer took a galley of type and scrambled.</p>
    <a class="btn" href="#">NEW PATIENT FORM</a>
  </section>

  <footer class="footer" role="img" aria-label="Soft background photo of pink blossoms">
    <h3 style="left:78px">QUICK INQUIRY</h3>
    <div class="field" style="top:103px">Name*</div>
    <div class="field" style="top:150px">Email*</div>
    <div class="field" style="top:196px">Services*</div>
    <div class="field" style="top:244px;height:92px">Message*</div>
    <div class="btn submit">SUBMIT</div>

    <h3 style="left:569px">OUR SERVICES</h3>
    <ul class="links">
      <li>Home</li><li>About Us</li><li>Services</li><li>Conditions We Treat</li><li>New Patients</li><li>Contact Us</li>
    </ul>

    <h3 style="left:873px">FIND US</h3>
    <div class="find" style="top:100px"><svg viewBox="0 0 24 24"><path d="M12 2a7 7 0 0 0-7 7c0 5 7 13 7 13s7-8 7-13a7 7 0 0 0-7-7z" fill="#fff"/><circle cx="12" cy="9" r="2.6" fill="#6b2c55"/></svg><span>Maplecrest Behavioral Healthcare<br>Lorem Ipsum is simply dummy<br>text printing and typesetting</span></div>
    <div class="find" style="top:186px"><svg viewBox="0 0 24 24"><path d="M5 3c0 9 6 16 15 16l1-4-4-2-2 2c-2.5-1-5-3.5-6-6l2-2-2-4z" fill="#fff"/></svg><span>+1-555-014-2280</span></div>
    <div class="find" style="top:226px"><svg viewBox="0 0 24 24"><rect x="3" y="9" width="18" height="11" fill="#fff"/><rect x="7" y="3" width="10" height="7" fill="none" stroke="#fff" stroke-width="2"/><rect x="7" y="13" width="10" height="2" fill="#6b2c55"/></svg><span>+1-555-014-2280</span></div>
    <div class="find" style="top:266px"><svg viewBox="0 0 24 24"><rect x="2" y="5" width="20" height="14" fill="#fff"/><path d="M2 5l10 8 10-8" stroke="#6b2c55" stroke-width="2" fill="none"/></svg><span>info@maplecresthealth.com</span></div>
  </footer>
  <div class="social" style="left:873px"></div>
  <div class="social" style="left:933px"></div>
  <div class="social" style="left:993px"></div>

  <div class="copyright">&copy; MAPLECREST BEHAVIORAL HEALTHCARE- 2017. All Rights Reserved</div>
</div>
</body>
</html>
```